Machining Business Order Thank You Insert

I am looking for a business style card to include with orders that I ship. The card needs to thank the recipient for their order, and encourage them to leave a review. The card should include my business name and contact information and have an area to hand write a message.

I mainly sale on Craftlane and my own website. We are a machining an manufacturing business that are in the sale of mostly metal machined and 3d printed plastic products.

The front of the card should include the following:
Logo: (attached)
Snapgram: https://www.snapgram.example/kelvomill/
Friendsbook: https://www.friendsbook.example/KelvoMill
Website: https://www.kelvomill.example/

The back of the card needs an area to write a message

Industry/Entity Type

3D Printing, Machining, Craftlane

Contact Information for Business Card

Black or white front, white back to write a personal message

Font styles to use
Sans Serif

Colors

Designer to choose colors to be used in the design.

Requirements
Must have
• Encourage a review, social media info

```html
<!DOCTYPE html>
<html lang="en">
<head>
<meta charset="utf-8">
<title>KelvoMill Order Thank You Card</title>
<link href="https://fonts.googleapis.com/css2?family=Saira+Semi+Condensed:wght@400;500;600&display=swap" rel="stylesheet">
<style>
  :root {
    --backdrop: #1d1d1e;
    --card-white: #ffffff;
    --ink-dark: #232323;
    --ink-gray: #6c6b6f;
    --text-gray: #55545a;
    --accent-orange: #ef6238;
    --rule: #8a8a8a;
  }
  * { box-sizing: border-box; margin: 0; padding: 0; }
  html, body { width: 1200px; height: 790px; overflow: hidden; }
  body {
    background: var(--backdrop);
    font-family: "Saira Semi Condensed", "Arial Narrow", sans-serif;
    position: relative;
  }
  .card {
    position: absolute;
    left: 337px;
    width: 480px;
    height: 274px;
    background: var(--card-white);
    padding: 5px;
  }
  .card--front { top: 125px; }
  .card--back { top: 422px; }
  .card__band {
    width: 100%;
    height: 100%;
    padding: 9px;
    position: relative;
  }
  .card--front .card__band {
    background: linear-gradient(to right, var(--ink-dark) 50.3%, var(--accent-orange) 50.3%);
  }
  .card--back .card__band {
    background: linear-gradient(to right, var(--ink-gray) 49.8%, var(--ink-dark) 49.8%);
  }
  .card__panel {
    width: 100%;
    height: 100%;
    background: var(--card-white);
    position: relative;
  }
  .brand-mark {
    position: absolute;
    left: 0; right: 0;
    display: flex;
    align-items: center;
    justify-content: center;
    gap: 10px;
  }
  .brand-mark__square {
    width: 18px; height: 18px;
    background: var(--ink-dark);
  }
  .brand-mark__name {
    color: var(--accent-orange);
    font-weight: 500;
    font-size: 30px;
    letter-spacing: 6px;
    line-height: 1;
  }
  .card--front .brand-mark { top: 40px; }
  .thanks {
    position: absolute;
    top: 94px;
    left: 0; right: 0;
    text-align: center;
  }
  .thanks__title {
    color: var(--ink-dark);
    font-weight: 600;
    font-size: 17px;
    line-height: 20px;
    letter-spacing: 0.5px;
  }
  .thanks__review {
    color: var(--text-gray);
    font-size: 12px;
    line-height: 16px;
  }
  .contact-list {
    position: absolute;
    top: 164px;
    left: 0; right: 0;
    text-align: center;
    color: var(--text-gray);
    font-size: 12px;
    line-height: 14px;
  }
  .contact-list__row { display: flex; justify-content: center; gap: 4px; }
  .contact-item { display: inline-flex; align-items: center; gap: 3px; }
  .contact-item svg { width: 8px; height: 8px; fill: var(--accent-orange); }
  .contact-item__dot {
    width: 8px; height: 8px; border-radius: 50%;
    background: var(--accent-orange);
    display: inline-block;
  }
  .card--back .brand-mark--symbol { top: 42px; }
  .brand-mark__block {
    width: 44px; height: 44px;
    background: var(--accent-orange);
  }
  .wordmark {
    position: absolute;
    top: 164px;
    left: 0; right: 0;
    text-align: center;
    color: var(--ink-gray);
    font-weight: 500;
    font-size: 22px;
    letter-spacing: 8px;
    line-height: 1;
  }
  .message-line {
    position: absolute;
    left: 20px; right: 18px;
    border-top: 1px dotted var(--rule);
  }
  .message-line--first { top: 207px; }
  .message-line--second { top: 232px; }
</style>
</head>
<body>

<section class="card card--front" aria-label="Card front">
  <div class="card__band">
    <div class="card__panel">
      <div class="brand-mark">
        <span class="brand-mark__square"></span>
        <span class="brand-mark__name">KELVOMILL</span>
      </div>
      <div class="thanks">
        <p class="thanks__title">Thank you for your order!</p>
        <p class="thanks__review">Loved it? Please leave us a review on Craftlane.</p>
      </div>
      <div class="contact-list">
        <div class="contact-list__row">
          <span class="contact-item">
            <svg viewBox="0 0 10 10"><path d="M5 0a3.5 3.5 0 0 0-3.5 3.5C1.5 6 5 10 5 10s3.5-4 3.5-6.5A3.5 3.5 0 0 0 5 0zm0 5a1.5 1.5 0 1 1 0-3 1.5 1.5 0 0 1 0 3z"/></svg>
            Ashford, IN
          </span>
          <span class="contact-item">
            <svg viewBox="0 0 10 10"><path d="M2 0.5l1.8 2.2-1 1.2a6 6 0 0 0 3.3 3.3l1.2-1L9.5 8 8.3 9.5C4 9.3.7 6 .5 1.7z"/></svg>
            555-214-7730
          </span>
        </div>
        <div class="contact-list__row">
          <span class="contact-item">
            <svg viewBox="0 0 10 10"><path d="M0 2h10v6H0z M0 2l5 3.5L10 2" fill="var(--accent-orange)" stroke="#fff" stroke-width="0.8"/></svg>
            kelvomillcnc@postbox.example
          </span>
          <span class="contact-item">
            <svg viewBox="0 0 10 10"><circle cx="5" cy="5" r="4.5"/><path d="M0.5 5h9M5 0.5c-2 2.5-2 6.5 0 9M5 0.5c2 2.5 2 6.5 0 9" stroke="#fff" stroke-width="0.7" fill="none"/></svg>
            www.kelvomill.example
          </span>
        </div>
        <div class="contact-list__row">
          <span class="contact-item"><span class="contact-item__dot"></span>@kelvomill.example</span>
          <span class="contact-item"><span class="contact-item__dot"></span>/kelvomill.example</span>
        </div>
      </div>
    </div>
  </div>
</section>

<section class="card card--back" aria-label="Card back">
  <div class="card__band">
    <div class="card__panel">
      <div class="brand-mark brand-mark--symbol">
        <span class="brand-mark__block"></span>
      </div>
      <div class="wordmark">KELVOMILL</div>
      <div class="message-line message-line--first"></div>
      <div class="message-line message-line--second"></div>
    </div>
  </div>
</section>

</body>
</html>
```